New web design for a service provider in the medical field

We are looking for a new design for our website. We are a company that repairs and sells medical endoscopes. Our customers include doctors and hospitals. Our current website can be found at https://lumavex.de/en/lumavex-english.
We need a new web design (without programming) for the following 3 pages:
-Startpage https://lumavex.de/en/lumavex-english/
-Used endoscopes https://lumavex.de/en/used-endoscopes/
-Purchase https://lumavex.de/en/purchase/
The design should be modern and stylish.
The blue color of the logo should be reflected on the page, but not too intrusive.
I have uploaded the images from the header. If more images are needed, let me know and I will upload them.

Target Market(s)
Doctors and hospitals

```html
<!DOCTYPE html>
<html lang="en">
<head>
<meta charset="utf-8">
<title>Lumavex – Purchase</title>
<link href="https://fonts.googleapis.com/css2?family=Roboto:wght@400;500;700&family=Ubuntu:wght@500;700&display=swap" rel="stylesheet">
<style>
:root{
  --navy:#1d3a52;
  --blue:#28a5dc;
  --ink:#1e2d3b;
  --muted:#5c6670;
  --field:#f4f4f4;
  --line:#dfe3e6;
  --white:#ffffff;
}
*{box-sizing:border-box;margin:0;padding:0}
html,body{width:1200px;height:3005px;overflow:hidden}
body{position:relative;font-family:"Roboto",sans-serif;color:var(--ink);background:var(--white)}
.abs{position:absolute}
.topbar{left:0;top:0;width:1200px;height:88px;background:var(--navy)}
.topbar .contact{top:8px;height:30px;display:flex;align-items:center;gap:12px;color:var(--white);font-size:14px}
.dot{width:30px;height:30px;border-radius:50%;background:var(--white);display:flex;align-items:center;justify-content:center;flex:none}
.social{display:flex;gap:7px}
.social span{width:32px;height:32px;border-radius:50%;display:block}
.top-social{left:980px;top:8px}
.top-social span{border:2px solid var(--white)}
.top-social span:first-child{background:var(--blue);border-color:var(--blue)}
.hero{left:0;top:88px;width:1200px;height:500px;background:linear-gradient(110deg,#b9c1c8 0%,#dde2e6 40%,#c8ced3 70%,#e7eaed 100%)}
.nav{left:73px;top:46px;width:1054px;height:86px;background:var(--white);border-radius:43px;display:flex;align-items:center;padding:0 37px 0 44px}
.brand{font-family:"Ubuntu",sans-serif;font-weight:700;font-size:22px;color:var(--navy);display:flex;align-items:center;gap:10px}
.brand i{width:12px;height:12px;border-radius:50%;background:var(--blue);display:block}
.menu{margin-left:auto;display:flex;gap:35px;font-size:15px;font-weight:700;color:var(--ink)}
.menu .active{color:var(--blue)}
.hero-title{left:109px;top:295px;font-family:"Ubuntu",sans-serif;font-weight:700;font-size:36px;line-height:44px;color:var(--white)}
.intro-bg{left:0;top:560px;width:1200px;height:543px;background:linear-gradient(180deg,#f7f9fb,#eef3f8)}
.intro-title{left:111px;top:716px;width:500px;font-family:"Ubuntu",sans-serif;font-size:20px;line-height:30px;font-weight:700;font-style:normal;color:var(--navy)}
.intro-title span{display:block;color:var(--blue)}
.intro-text{left:111px;top:798px;width:489px;font-size:13.5px;line-height:25.7px;color:var(--muted);text-align:justify}
.circle-accent{left:655px;top:575px;width:450px;height:450px;border-radius:50%;background:var(--blue)}
.circle-photo{left:660px;top:592px;width:428px;height:428px;border-radius:50%;background:radial-gradient(circle at 40% 40%,#dfe9f0,#9fc2d6 60%,#5c8fa8)}
.section-title{left:0;width:1200px;top:1190px;text-align:center;font-family:"Ubuntu",sans-serif;font-weight:700;font-size:31px;line-height:38px;color:var(--navy)}
.section-title span{color:var(--blue);display:block}
.group{left:224px;font-size:18px;font-weight:500;color:var(--navy)}
.label{font-size:14px;color:var(--ink)}
.label b{color:#e33;font-weight:400}
.field{width:368px;height:43px;background:var(--field);border:1px solid var(--line);font-size:13.5px;color:var(--muted);padding:0 16px;display:flex;align-items:center;justify-content:space-between}
.field.area{height:106px;align-items:flex-start;padding-top:14px}
.file{left:605px;top:2028px;width:120px;height:40px;border:1px solid var(--line);font-size:13.5px;color:var(--muted);display:flex;align-items:center;justify-content:center;background:var(--white)}
.note{left:605px;top:2082px;font-size:13px;line-height:22px;color:var(--muted)}
.btn{width:163px;height:49px;border-radius:25px 0 25px 25px;font-size:15px;font-weight:700;color:var(--white);display:flex;align-items:center;justify-content:center}
.help-bg{left:0;top:2310px;width:1200px;height:400px;background:linear-gradient(100deg,#2a9fd6,#3aa9df 50%,#2a97cf)}
.help-title{left:0;top:2370px;width:1200px;text-align:center;font-family:"Ubuntu",sans-serif;font-size:31px;font-weight:700;color:var(--white)}
.help-text{left:165px;top:2427px;width:870px;text-align:center;font-size:14.5px;line-height:26px;color:var(--white)}
.footer-bg{left:0;top:2640px;width:1200px;height:365px;background:var(--navy)}
.f-brand{left:111px;top:2805px;font-family:"Ubuntu",sans-serif;font-weight:700;font-size:28px;color:var(--white)}
.f-col h3{font-size:16px;font-weight:700;color:var(--white);margin-bottom:20px}
.f-col li{list-style:none;display:flex;align-items:center;gap:14px;font-size:14.5px;color:var(--white);height:31px}
.f-col li i{width:13px;height:13px;border-radius:50%;background:var(--blue);display:block}
.ci{display:flex;align-items:center;gap:20px;font-size:14.5px;line-height:23px;color:var(--white)}
.ci .dot{width:42px;height:42px}
.rule{left:111px;top:2952px;width:978px;height:1px;background:#3b5670}
.copy{left:0;width:1200px;top:2966px;text-align:center;font-size:13.5px;color:var(--white)}
.foot-social{left:976px;top:2958px}
.foot-social span{background:var(--white)}
.foot-social span:first-child{background:var(--blue)}
</style>
</head>
<body>

<div class="abs hero" role="img" aria-label="Close-up photograph of a flexible endoscope control body on a light surface"></div>
<div class="abs intro-bg"></div>

<svg class="abs" style="left:0;top:430px" width="1200" height="200" viewBox="0 0 1200 200">
  <path d="M0 130 C120 190 230 200 380 180 C560 150 720 30 900 30 C1030 30 1120 90 1200 130 L1200 200 L0 200Z" fill="#f7f9fb"/>
  <path d="M0 55 C110 135 230 160 380 148 C560 130 720 40 900 36 C1030 33 1120 80 1200 125" fill="none" stroke="#28a5dc" stroke-width="9"/>
</svg>

<header class="abs topbar">
  <div class="abs contact" style="left:111px">
    <span class="dot"><svg width="14" height="14" viewBox="0 0 24 24"><path fill="#28a5dc" d="M6.6 10.8a15 15 0 006.6 6.6l2.2-2.2c.3-.3.7-.4 1-.2 1.1.4 2.300.6 3.6.6.6 0 1 .4 1 1V20c0 .6-.4 1-1 1A17 17 0 013 4c0-.6.4-1 1-1h3.5c.6 0 1 .4 1 1 0 1.3.2 2.5.6 3.6.1.3 0 .7-.2 1z"/></svg></span>+49 4087 512 660-0
  </div>
  <div class="abs contact" style="left:312px">
    <span class="dot"><svg width="14" height="14" viewBox="0 0 24 24"><path fill="#28a5dc" d="M2 5h20v14H2z"/><path d="M2 6l10 7 10-7" fill="none" stroke="#fff" stroke-width="2"/></svg></span>info@lumavex.de
  </div>
  <div class="abs social top-social"><span></span><span></span><span></span></div>
</header>

<nav class="abs nav">
  <div class="brand"><i></i>Lumavex</div>
  <div class="menu">
    <span>HOME</span><span>USED ENDOSCOPES ⌄</span><span>ENDOSCOPY ACCESSORIES ⌄</span><span class="active">PURCHASE</span><span>CONTACT US</span>
  </div>
</nav>

<h1 class="abs hero-title">SUSTAINABLE AND<br>ECONOMICAL</h1>

<div class="abs circle-accent"></div>
<div class="abs circle-photo" role="img" aria-label="Photograph of a gloved hand holding an endoscope with a teal insertion tube"></div>

<h2 class="abs intro-title">DO YOU WANT TO SELL YOUR ENDOSCOPE?<span>YOU ARE AT THE RIGHT ADRESS!</span></h2>
<p class="abs intro-text">We are always interested in buying used endoscopes, accessories and peripherals from Orvantis, Kelmara and Teronel at fair conditions. We can promise you an objective offer with a clear conscience! Use the form below to offer us your device! If you want to have several devices checked, one of our technicians will usually come to you for the check. We also check defective and incomplete devices! We would be happy to take a look at your device!</p>

<h2 class="abs section-title">ARE YOU LOOKING TO REPLACE<span>YOUR FOR SALE DEVICE?</span></h2>

<form>
  <div class="abs group" style="top:1332px">PERSONAL INFORMATIONS:</div>
  <div class="abs label" style="left:226px;top:1383px">Salutation <b>*</b></div>
  <div class="abs field" style="left:226px;top:1413px">Choose<span>⌄</span></div>
  <div class="abs label" style="left:605px;top:1383px">Co. / dr. off <b>*</b></div>
  <div class="abs field" style="left:605px;top:1413px">Company / doctor's office</div>
  <div class="abs label" style="left:226px;top:1473px">Surname</div>
  <div class="abs field" style="left:226px;top:1503px">Surname</div>
  <div class="abs label" style="left:605px;top:1473px">Firstname</div>
  <div class="abs field" style="left:605px;top:1503px">Firstname</div>
  <div class="abs label" style="left:226px;top:1563px">Email <b>*</b></div>
  <div class="abs field" style="left:226px;top:1593px">Email</div>
  <div class="abs label" style="left:605px;top:1563px">Telephone</div>
  <div class="abs field" style="left:605px;top:1593px">Telephone</div>

  <div class="abs group" style="top:1686px">INFORMATIONS ABOUT THE DEVICE:</div>
  <div class="abs label" style="left:226px;top:1737px">Brand <b>*</b></div>
  <div class="abs field" style="left:226px;top:1767px">Choose<span>⌄</span></div>
  <div class="abs label" style="left:605px;top:1737px">Model <b>*</b></div>
  <div class="abs field" style="left:605px;top:1767px">Choose<span>⌄</span></div>
  <div class="abs label" style="left:226px;top:1827px">Defects / damage</div>
  <div class="abs field" style="left:226px;top:1857px">Defects / damage</div>
  <div class="abs label" style="left:605px;top:1827px">Asking price</div>
  <div class="abs field" style="left:605px;top:1857px">Asking price</div>

  <div class="abs group" style="top:1948px">REMARKS AND PICTURE:</div>
  <div class="abs label" style="left:226px;top:1998px">Remarks</div>
  <div class="abs field area" style="left:226px;top:2028px">Brief description of the error, other information, etc.</div>
  <div class="abs label" style="left:605px;top:1998px">Upload picture</div>
  <div class="abs file">Choose File</div>
  <div class="abs note">No file chosen allowed formats jpg, jpeg, png or bmp<br>maximum file size 4 MB</div>
  <div class="abs btn" style="left:519px;top:2173px;background:var(--blue)">SUBMIT NOW</div>
</form>

<section>
  <div class="abs help-bg" role="img" aria-label="Blue-tinted photograph of a technician repairing an endoscope"></div>
  <h2 class="abs help-title">HOW CAN WE HELP YOU?</h2>
  <p class="abs help-text">Good morning! We are looking forward for your message! You can get informations on possible or ongoing repairs of your endoscope technology. You can also get an advise on rational inspection intervals and in choosing the right accessories.</p>
  <div class="abs btn" style="left:519px;top:2507px;background:var(--navy)">SEND MESSAGE</div>
</section>

<footer>
  <div class="abs footer-bg"></div>
  <svg class="abs" style="left:0;top:2580px" width="1200" height="120" viewBox="0 0 1200 120">
    <path d="M0 20 C150 90 250 120 380 118 C600 112 800 20 980 20 C1080 20 1150 55 1200 85 L1200 120 L0 120Z" fill="#1d3a52"/>
    <path d="M0 20 C150 90 250 120 380 118 C600 112 800 20 980 20 C1080 20 1150 55 1200 85" fill="none" stroke="#fff" stroke-width="6"/>
  </svg>
  <div class="abs f-brand">Lumavex</div>
  <div class="abs f-col" style="left:369px;top:2738px"><h3>QUICK LINKS</h3><ul><li><i></i>Home</li><li><i></i>Endoscope Services</li><li><i></i>Endoscope Accessories</li><li><i></i>Purchase</li><li><i></i>Contact Us</li></ul></div>
  <div class="abs f-col" style="left:634px;top:2738px"><h3>OTHER LINKS</h3><ul><li><i></i>FAQ</li><li><i></i>Blog</li><li><i></i>Privacy Policy</li><li><i></i>Terms &amp; Conditions</li></ul></div>
  <div class="abs f-col" style="left:869px;top:2738px"><h3>CONTACT INFO</h3></div>
  <div class="abs ci" style="left:869px;top:2773px"><span class="dot"><svg width="14" height="16" viewBox="0 0 24 24"><path fill="#28a5dc" d="M12 2a7 7 0 00-7 7c0 5 7 13 7 13s7-8 7-13a7 7 0 00-7-7zm0 9.5A2.5 2.5 0 1112 6a2.5 2.5 0 010 5.5z"/></svg></span>Lindenweg 12, 21465<br>Hollbeck, Germany</div>
  <div class="abs ci" style="left:869px;top:2835px"><span class="dot"><svg width="14" height="14" viewBox="0 0 24 24"><path fill="#28a5dc" d="M6.6 10.8a15 15 0 006.6 6.6l2.2-2.2c.3-.3.7-.4 1-.2 1.1.4 2.3.6 3.6.6.6 0 1 .4 1 1V20c0 .6-.4 1-1 1A17 17 0 013 4c0-.6.4-1 1-1h3.5c.6 0 1 .4 1 1 0 1.3.2 2.5.6 3.6.1.3 0 .7-.2 1z"/></svg></span>+49 4087 512 660-0</div>
  <div class="abs ci" style="left:869px;top:2887px"><span class="dot"><svg width="14" height="14" viewBox="0 0 24 24"><path fill="#28a5dc" d="M2 5h20v14H2z"/><path d="M2 6l10 7 10-7" fill="none" stroke="#fff" stroke-width="2"/></svg></span>info@lumavex.de</div>
  <div class="abs rule"></div>
  <div class="abs copy">© 2022 <b>Lumavex</b> &nbsp;|&nbsp; All Rights Reserved</div>
  <div class="abs social foot-social"><span></span><span></span><span></span></div>
</footer>

</body>
</html>
```